Design a fun and engaging Social Media eBook

Graphic design job:

For initial concept stage, please provide some sample powerpoint designs of:
-A cover
-Section divides
-A few copy pages

We can then work on the full document which would be redesigning 22 pages of existing copy in word docs into the template.

Will be used to educate staff on Social Media.
We would like the design of the document to reflect the digital and social landscape. It should be fun and engaing.

Should demonstrate creativity, have social community focus, and be colourful and modern.

The audience is older people that need to be convinced about the benefits of social media and require some education / tips on how to use it. 40-60 year olds.

To be supplied to us in powerpoint.

Target Market(s)

Older staff that need to get the benefits of social media

Industry/Entity Type

Education

Requirements
Must have
• Must be supplied in Powerpoint.
Look modern, slick, cool, edgy

Look very "Quince" brand in simplicity and digital sense.
Reflect a 'digital' type of design

Combine all documents into one clean document / workbook.

(Don't worry will not be ised for powerpoint presentations, just want it in an edible document format - so lots of text on a slide is fine) Finished product will be a PDF
Nice to have
• Interactive in some way with click throughs or page turners

```html
<!DOCTYPE html>
<html lang="en">
<head>
<meta charset="utf-8">
<title>Building a Community &amp; Increasing Your Fans</title>
<link rel="stylesheet" href="https://fonts.googleapis.com/css2?family=Questrial&family=Montserrat:wght@400;600&display=swap">
<style>
  :root {
    --frame-dark: #1c1a17;
    --panel-white: #ffffff;
    --ink: #262626;
    --ink-soft: #3a3a3a;
    --ink-muted: #8c8c8c;
    --accent-red: #f01414;
    --footer-text: #a9a49d;
    --footer-icon: #d8d4ce;
    --band-violet: #d7b4f7;
    --band-blue: #aab8f2;
    --band-cyan: #bdf3f3;
    --band-green: #a9efaf;
    --band-green-deep: #86e58c;
    --figure-red: #e86a6a;
    --figure-yellow: #f3d25a;
    --figure-blue: #5b9be0;
    --figure-violet: #b86ad0;
    --button-top: #3a3a3a;
    --button-bottom: #050505;
  }
  * { box-sizing: border-box; margin: 0; padding: 0; }
  html, body {
    width: 1200px;
    height: 901px;
    overflow: hidden;
    background: var(--frame-dark);
    font-family: "Questrial", "Helvetica Neue", Arial, sans-serif;
  }
  .canvas {
    position: relative;
    width: 1200px;
    height: 901px;
    background: var(--frame-dark);
  }
  .page {
    position: absolute;
    left: 22px;
    top: 24px;
    width: 1159px;
    height: 790px;
    background: var(--panel-white);
    border-radius: 11px;
    overflow: hidden;
  }
  .wave-band {
    position: absolute;
    left: 0;
    top: 395px;
    width: 1159px;
    height: 327px;
    background: linear-gradient(90deg,
      var(--band-violet) 0%,
      var(--band-blue) 14%,
      var(--band-cyan) 45%,
      var(--band-green) 80%,
      var(--band-green-deep) 100%);
  }
  .community-illustration {
    position: absolute;
    left: 94px;
    top: 161px;
    width: 344px;
    height: 303px;
    border-radius: 14px;
    background: linear-gradient(135deg,
      var(--figure-yellow) 0%,
      var(--figure-red) 35%,
      var(--figure-violet) 65%,
      var(--figure-blue) 100%);
  }
  .headline {
    position: absolute;
    inset: 0;
    font-weight: 400;
    color: var(--ink);
    text-transform: uppercase;
  }
  .headline span { position: absolute; white-space: nowrap; line-height: 1; }
  .headline__building { left: 480px; top: 269px; font-size: 53px; letter-spacing: -0.5px; }
  .headline__community { left: 535px; top: 311px; font-size: 27px; color: var(--ink-soft); }
  .headline__ampersand {
    left: 719px; top: 244px; font-size: 110px; color: var(--accent-red);
    font-family: "Montserrat", "Helvetica Neue", Arial, sans-serif; font-weight: 400;
  }
  .headline__increasing { left: 788px; top: 297px; font-size: 44px; letter-spacing: -1.5px; color: var(--ink-soft); }
  .headline__fans { left: 886px; top: 329px; font-size: 24px; color: var(--ink-muted); }
  .cta-button {
    position: absolute;
    left: 698px;
    top: 412px;
    width: 123px;
    height: 38px;
    border-radius: 6px;
    background: linear-gradient(180deg, var(--button-top) 0%, var(--button-bottom) 55%);
    color: #ffffff;
    font-family: "Montserrat", "Helvetica Neue", Arial, sans-serif;
    font-weight: 600;
    font-size: 13.5px;
    display: flex;
    align-items: center;
    justify-content: center;
    letter-spacing: 0.2px;
    box-shadow: 0 1px 2px rgba(0,0,0,0.35);
  }
  .footer-nav {
    position: absolute;
    left: 49px;
    top: 827px;
    display: flex;
    align-items: flex-end;
    gap: 8px;
    color: var(--footer-text);
    font-size: 14px;
  }
  .footer-nav__icon { width: 39px; height: 33px; display: block; }
  .footer-nav__label { margin-bottom: 4px; }
  .footer-tagline {
    position: absolute;
    left: 0;
    width: 1200px;
    top: 834px;
    text-align: center;
    color: var(--footer-text);
    font-size: 13.5px;
  }
</style>
</head>
<body>
<main class="canvas">
  <section class="page">
    <div class="wave-band" role="img" aria-label="Flowing ribbons of violet, blue, cyan and green light across the page"></div>
    <div class="community-illustration" role="img" aria-label="Colourful clay figures in a group hug, representing community"></div>
    <h1 class="headline">
      <span class="headline__building">Building</span>
      <span class="headline__community">A Community</span>
      <span class="headline__ampersand">&amp;</span>
      <span class="headline__increasing">Increasing</span>
      <span class="headline__fans">Your Fans</span>
    </h1>
    <a class="cta-button">GET STARTED</a>
  </section>

  <nav class="footer-nav">
    <svg class="footer-nav__icon" viewBox="0 0 39 33" aria-hidden="true">
      <path d="M19.5 2 L2 16 L5 19 L19.5 7.5 L34 19 L37 16 Z" fill="var(--footer-icon)"/>
      <path d="M8 18 L19.5 9 L31 18 V31 H23 V22 H16 V31 H8 Z" fill="var(--footer-icon)"/>
      <rect x="28" y="4" width="4" height="8" fill="var(--footer-icon)"/>
    </svg>
    <span class="footer-nav__label">HOME</span>
  </nav>
  <p class="footer-tagline">Professional Wealth Management</p>
</main>
</body>
</html>
```